website update

We need to redesign our current website to be more personalised and sophisticated. We are physiotherapy clinic based in sydney australia, offer a range of clinical service such as Physiotherapy, Massage, sports injuries rehabilitation, Women's health (incontinency etc), Pilates classes, back pain exercise program, acupuncture, Gait analysis.
our current website is www.brightlanehealth.com.au
an example of ideal website is http://quillbrookrehabstudio.com/
homepage: with a revolving displaying attached photos which is linked to relevants page

```html
<!DOCTYPE html>
<html lang="en">
<head>
<meta charset="utf-8">
<title>brightlane Physiotherapy &amp; Sports Clinic</title>
<link href="https://fonts.googleapis.com/css2?family=Mulish:wght@400;500;600;700&display=swap" rel="stylesheet">
<style>
:root{
  --green:#8dc21f;
  --green-dark:#6fa515;
  --green-band:#a3c935;
  --panel-left:#c8df80;
  --panel-right:#eef3d0;
  --text:#4a4a4a;
  --muted:#7a7a7a;
  --icon-bg:#eef2d6;
  --icon-fg:#3d3d2a;
  --footer-bg:#f7f9f0;
}
*{margin:0;padding:0;box-sizing:border-box}
html,body{width:882px;height:1200px;overflow:hidden;background:#fff}
body{font-family:"Mulish",sans-serif;color:var(--text);position:relative}
.abs{position:absolute}

.brand{left:105px;top:18px;display:flex;align-items:center;gap:8px}
.brand-dot{width:52px;height:44px;border-radius:50%;background:var(--green)}
.brand-name{font-size:22px;font-weight:700;color:var(--green);line-height:1}
.brand-tag{font-size:7.5px;color:var(--muted);letter-spacing:.2px;margin-top:2px}

.contact{right:111px;top:28px;text-align:right}
.contact-phone{font-size:17px;color:var(--green-dark);font-weight:600;display:flex;align-items:center;gap:4px;justify-content:flex-end}
.contact-mail{font-size:8.5px;color:var(--muted);margin-top:4px}

.nav{left:106px;top:74px;width:670px;height:37px;background:linear-gradient(#9ccf2c,#84bb1c);display:flex;align-items:center;padding-left:28px;gap:24px;z-index:3}
.nav a{color:#fff;font-size:12px;text-decoration:none}

.hero{left:0;top:93px;width:882px;height:365px;background:linear-gradient(100deg,#c9c9c9 0%,#e6e6e6 30%,#d15a8e 48%,#3a3a3a 70%,#bdbdbd 100%)}
.dots{left:420px;top:407px;display:flex;gap:3px;z-index:2}
.dots span{width:9px;height:9px;border-radius:50%;background:#fff}
.dots span.on{background:var(--green)}

.page-fade{left:0;top:458px;width:882px;height:376px;background:linear-gradient(#e9e9e9,#fff 60%)}
.card{left:106px;top:429px;width:670px;height:405px;background:#fff;box-shadow:0 0 6px rgba(0,0,0,.06)}
.intro-title{left:131px;top:452px;font-size:20px;color:var(--green-dark);font-weight:500}
.intro-sub{left:131px;top:480px;font-size:14px;color:#444}
.intro-body{left:131px;top:505px;width:375px;font-size:8.4px;line-height:14.5px;color:var(--muted)}
.btn{left:130px;top:577px;width:80px;height:23px;background:linear-gradient(#9ccf2c,#80b61a);color:#fff;font-size:9px;font-weight:600;display:flex;align-items:center;justify-content:center;border-radius:2px}
.video{left:527px;top:450px;width:228px;height:147px;background:linear-gradient(120deg,#7b8592,#e8e8e8 55%,#2b2b2b);border-radius:2px}
.play{left:629px;top:508px;width:26px;height:26px;border-radius:50%;background:#222;border:2px solid #fff}
.rule{left:129px;top:625px;width:624px;height:1px;background:#ddd}

.feature{top:659px;width:150px;text-align:center}
.feature-icon{width:60px;height:60px;border-radius:50%;background:var(--icon-bg);margin:0 auto 8px}
.feature-title{font-size:12.5px;color:var(--green-dark);margin-bottom:5px}
.feature-text{font-size:8.3px;line-height:14.3px;color:var(--muted)}

.band{left:0;top:834px;width:882px;height:240px;background:var(--green-band)}
.band-head{top:857px;font-size:18px;color:#fff;letter-spacing:.3px}
.panel{top:887px;height:202px;padding:26px 0 0 26px}
.panel.left{left:106px;width:335px;background:var(--panel-left)}
.panel.right{left:441px;width:335px;background:var(--panel-right);padding-top:24px}
.panel ul{list-style:none}
.panel li{font-size:10.5px;color:#4f4f4f;height:23px;display:flex;align-items:center;gap:7px}
.panel li svg{flex:none}

.footer{left:0;top:1074px;width:882px;height:126px;background:var(--footer-bg)}
.foot-links{left:108px;top:1117px;font-size:10px;color:#444}
.foot-copy{left:108px;top:1139px;font-size:8.8px;color:#666}
.social{left:108px;top:1160px;display:flex;gap:2px}
.social span{width:20px;height:20px;border-radius:50%;background:#111}
.address{left:634px;top:1117px;font-size:9.2px;line-height:16.5px;color:#555}
</style>
</head>
<body>
<div class="abs brand">
  <div class="brand-dot"></div>
  <div>
    <div class="brand-name">brightlane</div>
    <div class="brand-tag">PHYSIOTHERAPY &amp; SPORTS CLINIC</div>
  </div>
</div>
<div class="abs contact">
  <div class="contact-phone">
    <svg width="18" height="18" viewBox="0 0 18 18"><circle cx="9" cy="9" r="8" fill="none" stroke="#6fa515" stroke-width="1.5"/><path d="M6 5l2 2-1 1.2c.6 1.3 1.5 2.2 2.8 2.8L11 10l2 2-1.2 1.2C8.5 12.8 5.2 9.5 4.8 6.2z" fill="#6fa515"/></svg>
    02 9000 1234
  </div>
  <div class="contact-mail">info@brightlanehealth.com.au</div>
</div>

<nav class="abs nav">
  <a>Home</a><a>About Us</a><a>Common Conditions</a><a>Treatments</a><a>Specialised Services</a><a>Workplace</a><a>Contact us</a>
</nav>

<div class="abs hero" role="img" aria-label="Slide photo: patient stretching on a Pilates reformer with a physiotherapist assisting"></div>
<div class="abs dots"><span class="on"></span><span></span><span></span><span></span></div>

<div class="abs page-fade"></div>
<div class="abs card"></div>
<h1 class="abs intro-title" style="font-weight:500">Mauris vel lacus vitae felis vestibulum</h1>
<h2 class="abs intro-sub" style="font-weight:400">Etiam est nunc venenatis in tristique eu imperdiet</h2>
<p class="abs intro-body">Vivamus porttitor purus nisi eleifend libero a tempus libero lectus feugiat felis Morbi diam mauris viverra in gravida eu mattis in ante Morbi eget arcu Morbi porta libero id ullamcorper nonummy nibh ligula pulvinar metus eget consectetuer augue nisi quis lacus Ut ac mi quis lacus mollis aliquam Curabitur iaculis tempus eros Curabitur vel mi s</p>
<div class="abs btn">READ MORE</div>
<div class="abs video" role="img" aria-label="Video still: physiotherapist treating a patient lying on a table"></div>
<svg class="abs" style="left:629px;top:508px" width="26" height="26" viewBox="0 0 26 26"><circle cx="13" cy="13" r="12" fill="#222" stroke="#fff" stroke-width="2"/><path d="M10.5 8.5v9l7-4.5z" fill="#fff"/></svg>
<div class="abs rule"></div>

<div class="abs feature" style="left:122px">
  <div class="feature-icon" role="img" aria-label="Physical therapy pictogram"></div>
  <div class="feature-title">Physical Therapy</div>
  <div class="feature-text">Eget consectetuer augue nisi quis lacus Ut ac mi quis lacus mollis aliquam Curabitur iaculis</div>
</div>
<div class="abs feature" style="left:286px">
  <div class="feature-icon" role="img" aria-label="Neck and back pain pictogram"></div>
  <div class="feature-title">Neck &amp; Back Pain</div>
  <div class="feature-text">Eget consectetuer augue nisi quis lacus Ut ac mi quis lacus mollis aliquam Curabitur iaculis</div>
</div>
<div class="abs feature" style="left:450px">
  <div class="feature-icon" role="img" aria-label="Treatment cross and leaf pictogram"></div>
  <div class="feature-title">Our Teatment</div>
  <div class="feature-text">Eget consectetuer augue nisi quis lacus Ut ac mi quis lacus mollis aliquam Curabitur iaculis</div>
</div>
<div class="abs feature" style="left:608px">
  <div class="feature-icon" role="img" aria-label="Swimmer pictogram for sport injuries"></div>
  <div class="feature-title">Sport Injuries</div>
  <div class="feature-text">Eget consectetuer augue nisi quis lacus Ut ac mi quis lacus mollis aliquam Curabitur iaculis</div>
</div>

<div class="abs band"></div>
<div class="abs band-head" style="left:113px">WE TREAT</div>
<div class="abs band-head" style="left:455px">WE OFFER</div>

<svg width="0" height="0" style="position:absolute"><defs><symbol id="tick" viewBox="0 0 12 10"><path d="M1 5.5l3.5 3.5L11 1.5" fill="none" stroke="#7d8a6a" stroke-width="2" stroke-linecap="round"/></symbol></defs></svg>

<div class="abs panel left">
  <ul>
    <li><svg width="11" height="9"><use href="#tick"/></svg>Back and low back pain</li>
    <li><svg width="11" height="9"><use href="#tick"/></svg>Neck pain and Headaches</li>
    <li><svg width="11" height="9"><use href="#tick"/></svg>Spinal/ Posture disorders</li>
    <li><svg width="11" height="9"><use href="#tick"/></svg>Sport injuries</li>
    <li><svg width="11" height="9"><use href="#tick"/></svg>Work Injuries/ Motor vehicle accident (whiplash)</li>
    <li><svg width="11" height="9"><use href="#tick"/></svg>Knee/shoulder pain</li>
    <li><svg width="11" height="9"><use href="#tick"/></svg>Arthritis</li>
  </ul>
</div>
<div class="abs panel right">
  <ul>
    <li><svg width="11" height="9"><use href="#tick"/></svg>Manual therapy and spinal manipulation</li>
    <li><svg width="11" height="9"><use href="#tick"/></svg>Acupuncture/Dry Needling</li>
    <li><svg width="11" height="9"><use href="#tick"/></svg>Electrical Therapy</li>
    <li><svg width="11" height="9"><use href="#tick"/></svg>Spinal strengthening (core stability training with real-time</li>
    <li><svg width="11" height="9"><use href="#tick"/></svg>Sports Injuries rehabilitation</li>
    <li><svg width="11" height="9"><use href="#tick"/></svg>Post Operative rehabilitation</li>
    <li><svg width="11" height="9"><use href="#tick"/></svg>Custom-made orthotics</li>
  </ul>
</div>

<div class="abs footer"></div>
<div class="abs foot-links">Home &nbsp;|&nbsp; About Us &nbsp;|&nbsp; Common Conditions &nbsp;|&nbsp; Treatments &nbsp;|&nbsp; Specialised Services &nbsp;|&nbsp; Contact us</div>
<div class="abs foot-copy">© 2014 Company Name &nbsp;All right reserved &nbsp;Term of Use</div>
<div class="abs social"><span></span><span></span><span></span><span></span></div>
<div class="abs address">Shop 3, The Arcade, 212<br>Harbour St, Lindfield 2070<br>Ryde: 02 9000 1234</div>
</body>
</html>
```